A New and modern Business Card for Tarwick Trade Solutions Ltd

New and modern Logo and Business Card Attached is the current logo/business card designCurrently the business is called "Tarwick & Co." or TTS Ltd for short. This is subject to change.This business specialises in Telecoms and Energy. We work with the major networks (QV, K7, etc) and also offer Energy Products saving clients money off their energy bills.These are business to business services.The current design incorporates a Pheonix, indicating rebirth, starting something new.We would like to maintain the Phoenix element but a newer modern style.We love colours in the logo 3 max.The aim of this is to be ultra slick and modern. I envisage Tarwick & Co. on one side of the card with long descriptions on the other side.Side 1:TTS Ltd/Logo?Side 2:TTS Ltd/Logo/Graphic?Tarwick & Co..Name:Address:Phone:Email:The design is mostly flexible but must incorporate a Phoenix.For example "Tarwick & Co." with a block phoenix behind the text...up to you.

Industry/Entity Type

Telecommunications

Contact Information for Business Card

Tarwick & Co.
Address:
Name:
Phone:
Email:

Logo Text

Tarwick & Co.

Colors
33a6d7
0792cd
acd037
9bcb3c
f78f20
fece3e

Requirements
Must have
• Phoenix
• 3/4 colours max
• Blue representing Technology (wireless)
• Green for Eco Energy
• Orange for Phoenix
• White business card background
Should not have
• phoenix must not all be red/ orange fire, we are a technology service company and the phoenix colours must represent this. Fire is not representative of our company.

```html
<!DOCTYPE html>
<html lang="en">
<head>
<meta charset="UTF-8">
<title>Tarwick &amp; Co. Business Card</title>
<link rel="stylesheet" href="https://fonts.googleapis.com/css2?family=Open+Sans:wght@400;700&display=swap">
<style>
  :root {
    --backdrop: #b3b3b3;
    --card: #ffffff;
    --ink: #1a1a1a;
    --ink-soft: #333333;
    --tech-blue: #0792cd;
    --rule: #222222;
  }
  * { margin: 0; padding: 0; box-sizing: border-box; }
  html, body {
    width: 1200px;
    height: 900px;
    overflow: hidden;
    background: var(--backdrop);
    font-family: "Open Sans", Arial, sans-serif;
  }
  .stage { position: relative; width: 1200px; height: 900px; }
  .card {
    position: absolute;
    left: 329px;
    width: 576px;
    height: 369px;
    background: var(--card);
    border-radius: 24px;
  }
  .card--front { top: 70px; }
  .card--back { top: 473px; }

  .front-mark {
    position: absolute;
    left: 30px;
    top: 160px;
    width: 180px;
    text-align: center;
    font-family: "Open Sans", Arial, sans-serif;
    font-weight: 700;
    font-size: 22px;
    line-height: 1.3;
    color: var(--ink);
  }

  .divider {
    position: absolute;
    left: 242px;
    top: 67px;
    width: 2px;
    height: 240px;
    background: var(--rule);
  }
  .person { position: absolute; left: 293px; top: 76px; }
  .person__name {
    font-weight: 700;
    font-size: 21px;
    color: var(--ink);
    letter-spacing: 0.2px;
  }
  .person__role { font-size: 13px; color: var(--ink-soft); margin-top: 2px; }

  .contacts { position: absolute; left: 293px; top: 142px; list-style: none; }
  .contacts li {
    display: flex;
    align-items: flex-start;
    font-size: 14.5px;
    line-height: 1.4;
    color: var(--ink-soft);
  }
  .contacts li + li { margin-top: 15px; }
  .contacts svg { flex: none; width: 19px; height: 19px; margin-right: 13px; margin-top: 1px; }

  .back-brand {
    position: absolute;
    inset: 0;
    display: flex;
    align-items: center;
    justify-content: center;
    gap: 20px;
  }
  .back-brand__dot {
    width: 40px;
    height: 40px;
    border-radius: 50%;
    background: var(--tech-blue);
  }
  .back-brand__name {
    font-family: "Open Sans", Arial, sans-serif;
    font-weight: 700;
    font-size: 46px;
    color: var(--ink);
  }
</style>
</head>
<body>
<main class="stage">
  <section class="card card--front">
    <div class="front-mark">Tarwick &amp; Co.</div>
    <div class="divider"></div>
    <div class="person">
      <p class="person__name">FNAME MNAME LNAME</p>
      <p class="person__role">Designation</p>
    </div>
    <ul class="contacts">
      <li>
        <svg viewBox="0 0 20 20" aria-hidden="true"><circle cx="10" cy="10" r="10" fill="#1a1a1a"/><path d="M7 5.5l1.6 0 .8 2.2-1 .9a6 6 0 0 0 3 3l.9-1 2.2.8v1.6c0 .6-.5 1-1.1 1A8 8 0 0 1 6 6.6c0-.6.4-1.1 1-1.1z" fill="#fff"/></svg>
        <span>123 456 789</span>
      </li>
      <li>
        <svg viewBox="0 0 20 20" aria-hidden="true"><circle cx="10" cy="10" r="10" fill="#1a1a1a"/><rect x="5" y="6.5" width="10" height="7" fill="#fff"/><path d="M5 6.5l5 4 5-4" fill="none" stroke="#1a1a1a" stroke-width="1.2"/></svg>
        <span>address@email.com</span>
      </li>
      <li>
        <svg viewBox="0 0 20 20" aria-hidden="true"><circle cx="10" cy="10" r="10" fill="#1a1a1a"/><path d="M10 4.5a3.5 3.5 0 0 1 3.5 3.5c0 2.6-3.5 7-3.5 7S6.5 10.6 6.5 8A3.5 3.5 0 0 1 10 4.5z" fill="#fff"/><circle cx="10" cy="8" r="1.3" fill="#1a1a1a"/></svg>
        <span>Address Address Address<br>Address Address</span>
      </li>
      <li>
        <svg viewBox="0 0 20 20" aria-hidden="true"><circle cx="10" cy="10" r="10" fill="#1a1a1a"/><circle cx="10" cy="10" r="5.5" fill="#fff"/></svg>
        <span>www.webaddress.com</span>
      </li>
    </ul>
  </section>

  <section class="card card--back">
    <div class="back-brand">
      <span class="back-brand__dot"></span>
      <span class="back-brand__name">Tarwick &amp; Co.</span>
    </div>
  </section>
</main>
</body>
</html>
```